Online interactive tutorial for year 2 to year 12 students in Australia

Website design for a new online tutorial for year 2 to year 12 students in Australia.

- The tutorial will be conducted via live webcam and within a dedicated interactive space
- The tutorial will be provided by high scoring undergraduates studying in top Australian universities.
- The tutors will be going through interviews & assessments & only top students are allowed to apply.
- Parents will do search and select tutor and have short 15 mins video interaction with potential tutors before booking them for their children for tutoring.
- hourly cost of booking (no monthly subscription or no hour limits)
- Tutors will have their own profile

Please see the attached for detailed page functionality.

The look and feel of the design must consider the following:
- must be educational but not dull and should stand out
- must appeal to younger generation - tutees (8-18 years), tutors (19-25), parents (30-50).
- Ideas for Logos (brivora.com.au but not confirmed)

Target Market(s)

tutees (8-18 years), tutors (19-25 years), parents (30-50 years).

Industry/Entity Type

Education

Coding

Coded - Design and coding required

Number of Pages Required

5+ page

Font styles to use
Serif

Requirements
Must have
• The look and feel of the design must consider the following:
• - must be educational but not dull and should stand out
• - must appeal to younger generation - tutees (8-18 years), tutors (19-25), parents (30-50).
Should not have
• Dullness

```html
<!DOCTYPE html>
<html lang="en">
<head>
<meta charset="utf-8">
<title>Brivora – Tutee Dashboard</title>
<link href="https://fonts.googleapis.com/css2?family=Open+Sans:wght@400;600;700&family=Oswald:wght@400;500&family=Roboto+Condensed:wght@400;700&family=Roboto:wght@400;500;700&display=swap" rel="stylesheet">
<style>
:root{
  --blue:#1a9fd4;
  --nav:#2b8fd6;
  --nav-dark:#2379b8;
  --heading:#1aa0c8;
  --red:#d9302c;
  --orange:#f5a20f;
  --green:#a5c63b;
  --dark:#333333;
  --darker:#2b2b2b;
  --text:#666666;
  --line:#dcdcdc;
  --cal-bg:#ececec;
  --cal-head:#555555;
  --white:#ffffff;
}
*{box-sizing:border-box;margin:0;padding:0}
html,body{width:1200px;height:2416px;overflow:hidden}
body{position:relative;background:var(--white);font-family:'Open Sans',sans-serif;color:var(--text)}
.abs{position:absolute}

/* header */
.site-header{position:absolute;top:0;left:0;width:1200px;height:116px;background:var(--white)}
.brand{position:absolute;left:100px;top:30px;display:flex;align-items:center;gap:12px}
.brand-dot{width:44px;height:44px;border-radius:50%;background:var(--blue)}
.brand-name{font-family:'Roboto',sans-serif;font-weight:700;font-size:40px;color:var(--dark)}
.search{position:absolute;left:362px;top:37px;width:360px;height:34px;border:1px solid #cfcfcf;display:flex}
.search-input{flex:1;font-size:12px;color:#555;padding:9px 12px;position:relative}
.search-input::after{content:"";position:absolute;right:12px;top:14px;border:4px solid transparent;border-top-color:#777}
.search-btn{width:38px;background:#e4e4e4;border-left:1px solid #cfcfcf;display:flex;align-items:center;justify-content:center}
.role-btn{position:absolute;top:38px;height:33px;border:2px solid var(--nav-dark);border-radius:2px;display:flex;align-items:center;justify-content:center;gap:7px;font-size:13px;color:var(--nav-dark)}
.login-btn{position:absolute;left:1032px;top:37px;width:68px;height:34px;background:var(--nav-dark);color:#fff;font-size:13px;font-weight:600;display:flex;align-items:center;justify-content:center;border-radius:2px}

.main-nav{position:absolute;top:116px;left:0;width:1200px;height:48px;background:var(--nav);display:flex;padding-left:92px}
.main-nav a{color:#fff;text-decoration:none;font-family:'Roboto',sans-serif;font-size:13px;font-weight:500;height:48px;line-height:48px;padding:0 30px;border-right:1px solid rgba(0,0,0,.12)}
.main-nav a:first-child{padding-left:30px}

/* hero */
.hero{position:absolute;top:164px;left:0;width:1200px;height:327px}
.hero-photo{position:absolute;inset:0;background:linear-gradient(180deg,#5b5450 0%,#3e3733 55%,#2f2a27 100%)}
.hero-title{position:absolute;top:150px;width:100%;text-align:center;font-family:'Roboto Condensed',sans-serif;font-weight:700;font-size:42px;color:#fff;text-shadow:0 2px 4px rgba(0,0,0,.4)}
.hero-edge{position:absolute;left:0;top:0}

/* schedules */
.section-title{font-family:'Roboto Condensed',sans-serif;font-size:27px;color:var(--heading);letter-spacing:.3px}
.title-bar{width:52px;height:4px;background:#777;margin-top:12px}
.schedule-list{position:absolute;left:100px;top:570px;width:475px}
.schedule-item{border-bottom:1px solid var(--line);padding:18px 0 12px}
.schedule-item:first-of-type{padding-top:20px}
.schedule-date{font-family:'Oswald',sans-serif;font-size:18px;color:var(--red)}
.schedule-text{font-size:14px;line-height:21px;color:var(--text);margin-top:5px}
.read-more{color:var(--heading);font-weight:700;font-size:12px}
.view-more{margin-top:20px;font-family:'Roboto',sans-serif;font-size:15px;color:var(--heading);display:flex;align-items:center;gap:6px}

.calendar-block{position:absolute;left:625px;top:570px;width:475px}
.calendar{margin-top:26px;width:475px}
.cal-head{display:flex;height:40px}
.cal-label{flex:1;background:var(--blue);color:#fff;font-family:'Oswald',sans-serif;font-size:20px;padding:7px 16px}
.cal-month{width:143px;background:var(--orange);color:#fff;font-family:'Oswald',sans-serif;font-size:20px;padding:7px 12px;display:flex;justify-content:space-between;align-items:center}
.cal-grid{display:grid;grid-template-columns:repeat(7,1fr);gap:0}
.cal-dow{background:var(--cal-head);color:#fff;font-family:'Oswald',sans-serif;font-size:13px;text-align:center;height:23px;line-height:23px;border-right:1px solid #777}
.cal-day{background:var(--cal-bg);height:51.5px;line-height:51.5px;text-align:center;font-family:'Oswald',sans-serif;font-size:17px;color:#555;border-right:1px solid #fff;border-bottom:1px solid #fff}
.cal-day.mark{color:var(--red);font-weight:500}

/* past sessions */
.sessions{position:absolute;top:1029px;left:0;width:1200px;height:482px;background:var(--green);overflow:hidden}
.sessions-bg{position:absolute;inset:0;background:linear-gradient(180deg,rgba(165,198,59,1) 0%,rgba(150,186,52,1) 60%,rgba(138,176,46,1) 100%)}
.sessions-title{position:absolute;top:60px;width:100%;text-align:center;font-family:'Roboto',sans-serif;font-size:32px;color:#fff}
.sessions-intro{position:absolute;top:108px;left:150px;width:900px;text-align:center;color:#fff;font-size:12px;line-height:23.5px}
.sessions-rule{position:absolute;top:192px;left:547px;width:106px;height:1px;background:rgba(255,255,255,.8)}
.session-card{position:absolute;top:243px}
.session-icon{position:absolute;width:136px;height:136px;border-radius:50%;background:#fff;border:4px solid var(--green);box-shadow:0 0 0 2px rgba(255,255,255,.6);display:flex;align-items:center;justify-content:center}
.session-body{position:absolute;left:163px;top:7px;width:310px}
.session-name{font-family:'Roboto',sans-serif;font-size:20px;color:#fff}
.session-text{margin-top:12px;color:#fff;font-size:12px;line-height:22.5px}
.session-btn{margin-top:14px;display:inline-block;background:#222;color:#fff;font-size:12px;padding:7px 12px;border-radius:2px}

/* tutors */
.tutors-title{position:absolute;top:1551px;width:100%;text-align:center;font-family:'Roboto Condensed',sans-serif;font-size:32px;color:#333;letter-spacing:.5px}
.tutors-bar{position:absolute;top:1603px;left:574px;width:52px;height:4px;background:var(--green)}
.tutor-card{position:absolute;top:1648px;width:226px;height:372px;border:1px solid #dedede;text-align:center}
.tutor-photo{position:absolute;left:18px;top:15px;width:188px;height:178px}
.tutor-name{position:absolute;top:214px;width:100%;font-family:'Oswald',sans-serif;font-size:17px;color:var(--red)}
.tutor-text{position:absolute;top:242px;left:18px;width:188px;font-size:14px;line-height:21px;color:var(--text)}
.tutor-btn{position:absolute;left:50px;top:318px;width:125px;height:36px;background:var(--orange);color:#fff;font-size:13px;font-weight:700;line-height:36px}

/* footer */
.site-footer{position:absolute;top:2073px;left:0;width:1200px;height:292px;background:var(--dark);color:#fff}
.footer-title{position:absolute;top:30px;font-family:'Roboto',sans-serif;font-size:17px;color:#fff}
.footer-col{position:absolute;font-size:13px;line-height:21px;color:#eee}
.contact-row{display:flex;gap:16px;align-items:flex-start}
.link-list{list-style:none}
.link-list li{height:21.6px;line-height:21.6px;padding-left:18px;position:relative;font-size:13px}
.link-list li::before{content:"";position:absolute;left:2px;top:7px;border:4px solid transparent;border-left:5px solid #ddd}
.news-input{width:294px;height:41px;background:#fff;color:#555;font-size:12px;padding:12px 14px;margin-top:18px}
.news-btn{width:102px;height:40px;background:var(--blue);color:#fff;font-size:12px;font-weight:600;text-align:center;line-height:40px;margin-top:11px}
.social-row{display:flex;align-items:center;gap:12px;height:36.5px;font-size:14px}
.social-dot{width:26px;height:26px;border-radius:50%;border:2px solid #ddd}
.copyright{position:absolute;top:2365px;left:0;width:1200px;height:51px;background:var(--blue);color:#fff;font-size:12px;text-align:center;line-height:51px}
</style>
</head>
<body>

<header class="site-header">
  <div class="brand"><span class="brand-dot"></span><span class="brand-name">Brivora</span></div>
  <div class="search">
    <div class="search-input">Search</div>
    <div class="search-btn">
      <svg width="14" height="14" viewBox="0 0 14 14"><circle cx="6" cy="6" r="4.2" fill="none" stroke="#333" stroke-width="2"/><line x1="9" y1="9" x2="13" y2="13" stroke="#333" stroke-width="2"/></svg>
    </div>
  </div>
  <div class="role-btn" style="left:744px;width:79px">
    <svg width="12" height="14" viewBox="0 0 12 14"><circle cx="6" cy="4" r="3" fill="#2379b8"/><path d="M0 14c0-4 2.5-6 6-6s6 2 6 6z" fill="#2379b8"/></svg>Tutor</div>
  <div class="role-btn" style="left:831px;width:84px">
    <svg width="14" height="14" viewBox="0 0 14 14"><circle cx="4" cy="3.5" r="2.5" fill="#2379b8"/><circle cx="10" cy="3.5" r="2.5" fill="#2379b8"/><rect x="1" y="7" width="5" height="7" fill="#2379b8"/><rect x="8" y="7" width="5" height="7" fill="#2379b8"/></svg>Parent</div>
  <div class="role-btn" style="left:928px;width:92px">
    <svg width="12" height="14" viewBox="0 0 12 14"><circle cx="6" cy="4" r="3" fill="#2379b8"/><path d="M0 14c0-4 2.5-6 6-6s6 2 6 6z" fill="#2379b8"/></svg>Tutees</div>
  <div class="login-btn">LOGIN</div>
</header>

<nav class="main-nav">
  <a>HOME</a><a>TUTOR PROFILES</a><a>HOW IT WORKS</a><a>TESTIMONIALS</a><a>PRICES</a><a style="border-right:0">CONTACT US</a>
</nav>

<section class="hero">
  <div class="hero-photo" role="img" aria-label="Desk scene with keyboard, notepad, pen, mouse and a plant, darkened"></div>
  <h1 class="hero-title">TUTEE LOGGED</h1>
  <svg class="hero-edge" width="1200" height="327" viewBox="0 0 1200 327">
    <polygon points="0,258 600,324 1200,258 1200,327 0,327" fill="#ffffff"/>
    <polyline points="0,256 600,322 1200,256" fill="none" stroke="#1a9fd4" stroke-width="5"/>
  </svg>
</section>

<section class="schedule-list">
  <h2 class="section-title">UPCOMING SCHEDULES</h2>
  <div class="title-bar"></div>
  <div class="schedule-item">
    <div class="schedule-date">SEP 05, 2016</div>
    <p class="schedule-text">Aenean a nibh eget turpis vehicula tempus ac sed massa congue habitant morbi tristique senectus et netus..<span class="read-more">Read More</span></p>
  </div>
  <div class="schedule-item">
    <div class="schedule-date">SEP 14, 2016</div>
    <p class="schedule-text">Aenean a nibh eget turpis vehicula tempus ac sed massa congue habitant morbi tristique senectus et netus..<span class="read-more">Read More</span></p>
  </div>
  <div class="schedule-item">
    <div class="schedule-date">SEP 19, 2016</div>
    <p class="schedule-text">Aenean a nibh eget turpis vehicula tempus ac sed massa congue habitant morbi tristique senectus et netus..<span class="read-more">Read More</span></p>
  </div>
  <div class="view-more">VIEW MORE
    <svg width="12" height="12" viewBox="0 0 12 12"><circle cx="6" cy="6" r="6" fill="#1aa0c8"/><path d="M5 3.5l2.5 2.5L5 8.5" fill="none" stroke="#fff" stroke-width="1.6"/></svg>
  </div>
</section>

<section class="calendar-block">
  <h2 class="section-title">PAST SCHEDULES</h2>
  <div class="title-bar"></div>
  <div class="calendar">
    <div class="cal-head">
      <div class="cal-label">CALANDER</div>
      <div class="cal-month">SEP 2016
        <svg width="30" height="16" viewBox="0 0 30 16"><path d="M9 2L3 8l6 6M21 2l6 6-6 6" fill="none" stroke="#fff" stroke-width="2.6"/></svg>
      </div>
    </div>
    <div class="cal-grid">
      <div class="cal-dow">S</div><div class="cal-dow">M</div><div class="cal-dow">T</div><div class="cal-dow">W</div><div class="cal-dow">T</div><div class="cal-dow">T</div><div class="cal-dow" style="border-right:0">T</div>
      <div class="cal-day"></div><div class="cal-day"></div><div class="cal-day"></div><div class="cal-day"></div><div class="cal-day">1</div><div class="cal-day">2</div><div class="cal-day">3</div>
      <div class="cal-day">4</div><div class="cal-day mark">5</div><div class="cal-day">6</div><div class="cal-day">7</div><div class="cal-day">8</div><div class="cal-day mark">9</div><div class="cal-day">10</div>
      <div class="cal-day">11</div><div class="cal-day">12</div><div class="cal-day">13</div><div class="cal-day mark">14</div><div class="cal-day">15</div><div class="cal-day">16</div><div class="cal-day">17</div>
      <div class="cal-day">18</div><div class="cal-day">19</div><div class="cal-day">20</div><div class="cal-day">21</div><div class="cal-day">22</div><div class="cal-day">23</div><div class="cal-day">24</div>
      <div class="cal-day">25</div><div class="cal-day">26</div><div class="cal-day">27</div><div class="cal-day">28</div><div class="cal-day">29</div><div class="cal-day">30</div><div class="cal-day"></div>
    </div>
  </div>
</section>

<section class="sessions">
  <div class="sessions-bg" role="img" aria-label="Faint city skyline behind a green overlay"></div>
  <h2 class="sessions-title">PAST SESSIONS</h2>
  <p class="sessions-intro">Sed ut perspiciatis unde omnis iste natus error sit voluptatem accusantium doloremque laudantium, totam rem aperiam, eaque ipsa quae ab illo inventore veritatis et quasi architecto beatae vitae dicta sunt explicabo. Nemo enim ipsam voluptatem quia voluptas sit aspernatur aut odit aut fugit, sed quia consequuntur magni dolores eos qui ratione voluptatem sequi nesciunt. Neque porro quisquam est, qui dolorem ipsum quia dolor sit amet</p>
  <div class="sessions-rule"></div>

  <div class="session-card" style="left:104px">
    <div class="session-icon">
      <svg width="58" height="58" viewBox="0 0 58 58"><path d="M5 5h40l8 8v40H5z" fill="none" stroke="#a5c63b" stroke-width="4" stroke-linejoin="round"/><rect x="15" y="5" width="24" height="15" fill="none" stroke="#a5c63b" stroke-width="4"/><rect x="30" y="9" width="5" height="7" fill="#a5c63b"/><rect x="13" y="30" width="32" height="23" fill="none" stroke="#a5c63b" stroke-width="4"/></svg>
    </div>
    <div class="session-body">
      <h3 class="session-name">SAVED WORK</h3>
      <p class="session-text">sed do eiusmod tempor incididunt ut labore et dolore magna aliqua. Ut enim ad minim veniam, quis nostrud exercitation ullamco laboris nisi ut aliquip ex ea mmodo consequat. Duis aute irure dolor</p>
      <span class="session-btn">SAVED WORK</span>
    </div>
  </div>

  <div class="session-card" style="left:629px">
    <div class="session-icon">
      <svg width="62" height="62" viewBox="0 0 62 62"><rect x="6" y="8" width="38" height="48" fill="none" stroke="#a5c63b" stroke-width="4"/><line x1="13" y1="20" x2="34" y2="20" stroke="#a5c63b" stroke-width="3"/><line x1="13" y1="28" x2="34" y2="28" stroke="#a5c63b" stroke-width="3"/><line x1="13" y1="36" x2="30" y2="36" stroke="#a5c63b" stroke-width="3"/><line x1="13" y1="44" x2="26" y2="44" stroke="#a5c63b" stroke-width="3"/><path d="M54 6l5 5-22 24-7 2 2-7z" fill="none" stroke="#a5c63b" stroke-width="3.5" stroke-linejoin="round"/></svg>
    </div>
    <div class="session-body">
      <h3 class="session-name">DOCUMENT</h3>
      <p class="session-text">sed do eiusmod tempor incididunt ut labore et dolore magna aliqua. Ut enim ad minim veniam, quis nostrud exercitation ullamco laboris nisi ut aliquip ex ea mmodo consequat. Duis aute irure dolor</p>
      <span class="session-btn">DOCUMENT</span>
    </div>
  </div>
</section>

<h2 class="tutors-title">LIST OF FAVOURITE TUTORS</h2>
<div class="tutors-bar"></div>

<article class="tutor-card" style="left:113px">
  <div class="tutor-photo" role="img" aria-label="Portrait photo of a favourite tutor" style="background:linear-gradient(180deg,#d9d9d9,#9a8278 70%,#6a2e2e)"></div>
  <h3 class="tutor-name">NAME HEADING</h3>
  <p class="tutor-text">Aenean a nibh eget turpis vehicula tempus ac sed massa congue..</p>
  <div class="tutor-btn">MORE INFO</div>
</article>
<article class="tutor-card" style="left:364px">
  <div class="tutor-photo" role="img" aria-label="Portrait photo of a favourite tutor" style="background:linear-gradient(180deg,#8a8a8a,#c9aa8f 60%,#f2f2f2)"></div>
  <h3 class="tutor-name">NAME HEADING</h3>
  <p class="tutor-text">Aenean a nibh eget turpis vehicula tempus ac sed massa congue..</p>
  <div class="tutor-btn">MORE INFO</div>
</article>
<article class="tutor-card" style="left:615px">
  <div class="tutor-photo" role="img" aria-label="Portrait photo of a favourite tutor" style="background:linear-gradient(180deg,#e6e6e6,#b88e74 55%,#1f2530)"></div>
  <h3 class="tutor-name">NAME HEADING</h3>
  <p class="tutor-text">Aenean a nibh eget turpis vehicula tempus ac sed massa congue..</p>
  <div class="tutor-btn">MORE INFO</div>
</article>
<article class="tutor-card" style="left:865px">
  <div class="tutor-photo" role="img" aria-label="Portrait photo of a favourite tutor" style="background:linear-gradient(180deg,#d2d2d2,#c49a78 55%,#f0ece8)"></div>
  <h3 class="tutor-name">NAME HEADING</h3>
  <p class="tutor-text">Aenean a nibh eget turpis vehicula tempus ac sed massa congue..</p>
  <div class="tutor-btn">MORE INFO</div>
</article>

<footer class="site-footer">
  <h4 class="footer-title" style="left:98px">CONTACT US</h4>
  <div class="footer-col" style="left:98px;top:74px;width:260px">
    <p>Level 3, 22 Harbour Lane, Brisbane<br>QLD 4000, Australia</p>
    <div class="contact-row" style="margin-top:11px">
      <svg width="18" height="18" viewBox="0 0 18 18"><path d="M4 1l3 4-2 2c1 2 3 4 5 5l2-2 4 3-2 3C8 16 2 10 1 4z" fill="none" stroke="#ddd" stroke-width="1.3"/></svg>
      <p>Phone : +61 7 3000 1245<br>Fax : +61 7 3000 1246</p>
    </div>
    <div class="contact-row" style="margin-top:11px">
      <svg width="18" height="14" viewBox="0 0 18 14"><rect x="1" y="1" width="16" height="12" fill="none" stroke="#ddd" stroke-width="1.3"/><path d="M1 1l8 7 8-7" fill="none" stroke="#ddd" stroke-width="1.3"/></svg>
      <p>Email: info@brivora.com.au</p>
    </div>
  </div>

  <h4 class="footer-title" style="left:424px">USEFUL LINKS</h4>
  <ul class="footer-col link-list" style="left:424px;top:82px">
    <li>Home</li><li>About Us</li><li>Services</li><li>Tutor Profile</li><li>How It Works</li><li>Scheduler</li><li>Testimonials</li><li>Contact Us</li>
  </ul>

  <h4 class="footer-title" style="left:623px">JOIN OUR NEWSLETTER</h4>
  <div class="footer-col" style="left:623px;top:72px;width:300px">
    <p style="font-size:11px;line-height:20px">Sed ut perspiciatis unde omnis iste natus error sit volup-<br>tatem accusantium doloremque laudantium.</p>
    <div class="news-input">Enter Name</div>
    <div class="news-btn">SUBSCRIBE</div>
  </div>

  <h4 class="footer-title" style="left:1006px">SOCIAL</h4>
  <div class="footer-col" style="left:1004px;top:76px">
    <div class="social-row"><span class="social-dot"></span>Friendly</div>
    <div class="social-row"><span class="social-dot"></span>Chirper</div>
    <div class="social-row"><span class="social-dot"></span>Searchly+</div>
    <div class="social-row"><span class="social-dot"></span>vidstream</div>
  </div>
</footer>
<div class="copyright">Copyright 2016 | All Rights Reserved -- Brivora</div>

</body>
</html>
```